Lumavento business card

We need a modern business card - With our 4 colors - See web: www.lumavento.dk

I have attached logo and som old business Cards we have - Lets Make the new ones shine...:-) -

Industry/Entity Type

Business

Requirements
Must have
• the logo with lumavento only,

```html
<!DOCTYPE html>
<html lang="da">
<head>
<meta charset="utf-8">
<title>Lumavento business card</title>
<link href="https://fonts.googleapis.com/css2?family=Open+Sans:wght@400;600;700&display=swap" rel="stylesheet">
<style>
  :root {
    --backdrop: #3a3b3f;
    --paper: #ffffff;
    --orange: #f5861f;
    --lime: #a8c93a;
    --purple: #761a74;
    --magenta: #e8078c;
    --ink: #333333;
    --ink-soft: #555555;
  }
  * { margin: 0; padding: 0; box-sizing: border-box; }
  html, body {
    width: 1200px; height: 864px; overflow: hidden;
    background: var(--backdrop);
    font-family: "Open Sans", Arial, sans-serif;
  }
  .card {
    position: absolute; left: 320px;
    width: 560px; height: 320px;
    background: var(--paper);
    box-shadow: 0 10px 28px rgba(0,0,0,.45);
    overflow: hidden;
  }
  .card--front { top: 60px; }
  .card--back { top: 470px; }

  /* front */
  .colour-bands {
    position: absolute; left: 0; right: 0; bottom: 0; height: 175px;
    display: flex;
  }
  .colour-bands span { flex: 1; }
  .band--orange { background: var(--orange); }
  .band--lime { background: var(--lime); }
  .band--purple { background: var(--purple); }
  .band--magenta { background: var(--magenta); }
  .address-line {
    position: absolute; left: 0; right: 0; bottom: 52px;
    text-align: center; color: var(--paper);
    font-size: 15px; letter-spacing: .2px;
  }

  /* back */
  .brand {
    position: absolute; left: 40px; top: 42px; width: 180px;
    text-align: center;
  }
  .brand-name {
    display: flex; align-items: center; justify-content: center; gap: 8px;
    color: var(--lime); font-weight: 600; font-size: 20px; letter-spacing: 2px;
  }
  .brand-dot { width: 12px; height: 12px; border-radius: 50%; background: var(--lime); }
  .brand-rule { height: 2px; background: var(--lime); margin: 8px 0 5px; }
  .brand-tagline { font-size: 10px; color: var(--ink); }

  .person { position: absolute; left: 48px; top: 130px; }
  .person-name { color: var(--lime); font-weight: 700; font-size: 24px; line-height: 1.1; }
  .person-title { color: var(--ink); font-size: 15px; }

  .contact-list {
    position: absolute; left: 52px; top: 212px;
    list-style: none; color: var(--ink); font-size: 15px;
  }
  .contact-list li { display: flex; align-items: center; gap: 9px; height: 24px; }
  .contact-list svg { width: 13px; height: 13px; fill: none; stroke: var(--lime); stroke-width: 2; }
</style>
</head>
<body>

<section class="card card--front" aria-label="Card front">
  <div class="colour-bands">
    <span class="band--orange"></span>
    <span class="band--lime"></span>
    <span class="band--purple"></span>
    <span class="band--magenta"></span>
  </div>
  <p class="address-line">Lindevej 14 - 2000 Frederiksberg - Tlf. 33 12 45 67</p>
</section>

<section class="card card--back" aria-label="Card back">
  <div class="brand">
    <div class="brand-name"><span class="brand-dot"></span>lumavento</div>
    <div class="brand-rule"></div>
    <div class="brand-tagline">Medier til unge</div>
  </div>

  <div class="person">
    <p class="person-name">Maren Solvik</p>
    <p class="person-title">Managing Director</p>
  </div>

  <ul class="contact-list">
    <li>
      <svg viewBox="0 0 16 16" aria-hidden="true"><path d="M4 2l3 3-2 2c1 2 2 3 4 4l2-2 3 3-2 2C7 14 2 9 2 4z" fill="var(--lime)" stroke="none"/></svg>
      +45 40 12 34 56
    </li>
    <li>
      <svg viewBox="0 0 16 16" aria-hidden="true"><rect x="1.5" y="3.5" width="13" height="9"/><path d="M1.5 3.5l6.5 5 6.5-5"/></svg>
      ms@lumavento.dk
    </li>
    <li>
      <svg viewBox="0 0 16 16" aria-hidden="true"><path d="M7 9l2-2M5.5 8.5l-2 2a2 2 0 003 3l2-2M10.5 7.5l2-2a2 2 0 00-3-3l-2 2"/></svg>
      www.lumavento.dk
    </li>
  </ul>
</section>

</body>
</html>
```